Bold, Modern, Clean "Kestrelwaymassage.com" website

Why we stand out?
We are a male and female mobile massage team. Our names are Paul and Lina. 
Kestrel Way is a Seattle based mobile massage service. Our massage is offered to the community with a goal of facilitating balance within each individual. We specialize in integrated Pain management, and sports/medical massage therapy. Every client's first assessment is attended by our male and female massage therapist team. Depending on the goals identified for an individual determines which therapist will be assigned to provide treatment, if not both.

Our passion...
Here at Kestrel Way, we have a great passion for Postural Resoration and how it is integrated into an individual's Massage treatment. We pride ourselves in being natural facilitators of healing, which takes the ego of the therapist out of the client's healing process. We strive to deliver the best massage possible by including modalities such as Neuromuscular, Myofascial release, spontaneous muscle release, postural restoration, orthopedic, and medical massage.

Our education...

We are both Graduates of Venmora, school of massage therapy. We have continuing education in medical massage, myofacial release, trigger point therapy, postural restoration, anatomy, and spontaneous muscle release. Lina is also a Certified Yoga Instructor, which amplifies her experience with flexibility and strength as it pertains to each individual. Paul's passion is Massage, stretching, and strength training to encourage postural restoration and realignment.

Our rates-

Our rates are $75/ 60 minutes, $95/ 90 minutes, and $120/ 120 minutes.

Education-
Both Lina and I worked as behavioral health professionals that specialized in life skills mentoring for youth who had experienced different types of trauma. This led us both to want to help others in a different environment, where individuals can be empowered to take responsibility over their own healing. To us, massage is a type of manipulation physical therapy, that encourages healing on many levels.

Advice to any massage client-
The most important thing to 'us', as Licenced providers is to get you on to our table to show you our skills. But a good therapist never forgets that it's not about what we do for you, but what we can facilitate for you. Your health and healing has nothing to do with us. It is yours, not ours. Identify what your goals are with any Therapist, and know what the end looks like. Progress should be tangible, such as range of motion, and decreased pain.

Lina and Paul at Kestrel Way are awesome! I recently had open heart surgery, and Lina worked on me to increase my range of motion while helping with the pinched nerve from my arm being in the same position for so long during my surgery. My wife drives a lot for work, and Paul has helped decrease her neck and lower back pain immensely. They are seriously the best therapists I have ever worked with. I would recommend them to anyone who needs anything from stress relief to a medical massage treatment. They are professional, up beat, easy going, and always on time. And, I love that they meet us where ever we like! We did a staycation recently, where they came to our hotel to give us relaxation massages. Although usually they come to our home, where we focus on pain related issues. We will continue to work with them for a long, long time.

Target Market(s)

Mobile massage therapy clients

Industry/Entity Type

Massage Therapy

Coding

Coded - Design and coding required

Number of Pages Required

1 page

Font styles to use
Serif
Sans Serif

Requirements
Must have
• Please add or remove any information that would help the presentation of our website. Our logo is posted below, please include into the website.
• Please include a contact field that includes, kestrelwaymassage@fernmail.net,
• (206) 555-0148
• We have also included our own stock photos, as well as a photo of Paul and Lina. Please include a cropped photo of both massage therapists.

```html
<!DOCTYPE html>
<html lang="en">
<head>
<meta charset="utf-8">
<title>Kestrel Way – Mobile Massage</title>
<link rel="stylesheet" href="https://fonts.googleapis.com/css2?family=Abel&family=Kaushan+Script&family=Kreon:wght@400;700&family=Lato:wght@300;400;700&display=swap">
<style>
:root{
  --red:#bf4d4b;
  --red-dark:#a83e3d;
  --red-light:#d86c69;
  --navy:#1c1a8f;
  --footer:#26216b;
  --orange:#e8914a;
  --grey-bg:#f2f2f2;
  --text:#333;
  --muted:#8a8a8a;
  --link:#1c2aa8;
  --white:#fff;
}
*{box-sizing:border-box;margin:0;padding:0}
html,body{width:1200px;height:2406px;overflow:hidden;background:#fff}
body{font-family:"Lato",Arial,sans-serif;color:var(--text)}
.page{position:relative;width:1200px;height:2406px;overflow:hidden}
.abs{position:absolute}

/* top bar */
.quick-btn{left:82px;top:18px;width:151px;height:37px;border-radius:19px;background:var(--navy);color:#fff;font-size:14px;font-weight:700;display:flex;align-items:center;justify-content:center;gap:7px}
.top-contact{top:24px;font-size:13px;color:#222;display:flex;align-items:center;gap:8px;white-space:nowrap}

/* nav */
.nav{left:0;top:71px;width:1200px;height:57px;background:var(--red);border-top:2px solid var(--red-dark);border-bottom:2px solid var(--red-dark)}
.nav::before,.nav::after{content:"";position:absolute;left:0;right:0;border-top:1px dashed rgba(255,255,255,.45)}
.nav::before{top:5px}.nav::after{bottom:5px}
.nav-item{position:absolute;top:19px;font-size:14px;color:#fff;letter-spacing:.5px}
.nav-item.active{color:#f6b98c}
.nav-star{position:absolute;top:18px;font-size:13px;color:#fff}
.brand{left:528px;top:24px;width:144px;height:144px;border-radius:50%;background:var(--navy);border:5px solid #fff;box-shadow:0 0 0 2px var(--navy);display:flex;align-items:center;justify-content:center;text-align:center;color:#fff;font-family:"Kreon",Georgia,serif;font-weight:700;font-size:27px;line-height:1;z-index:3}

/* hero */
.hero{left:0;top:128px;width:1200px;height:533px;background:linear-gradient(90deg,#e9dccd 0%,#c6b39a 14%,#f3efe8 26%,#fbfaf8 45%,#f1ddd0 62%,#d7a688 75%,#e6c3ab 88%,#f5f2ee 100%)}
.hero-title{left:289px;top:196px;font-family:"Kaushan Script",cursive;font-size:62px;color:var(--red)}
.hero-sub{left:306px;top:270px;font-family:"Kreon",Georgia,serif;font-size:62px;color:var(--orange)}
.hero-tag{left:359px;top:344px;font-size:27px;color:#222}

/* section heads */
.sec-title{left:0;width:1200px;text-align:center;font-family:"Kreon",Georgia,serif;font-weight:700;font-size:30px;letter-spacing:.5px}
.sec-title .r{color:var(--red)}.sec-title .n{color:var(--navy)}
.divider{left:460px;width:280px;height:24px}

/* about */
.about-intro{left:80px;top:778px;width:1040px;text-align:center;font-size:12.5px;line-height:19px;color:#222}
.about-photo{left:64px;top:890px;width:489px;height:294px;background:radial-gradient(ellipse at 40% 55%,#c73a5c 0%,#e07a8e 28%,#8c8a80 52%,#fff 75%)}
.feature-icon{left:606px;width:80px;height:80px;border-radius:50%;background:var(--red);border:4px solid #fff;box-shadow:0 0 0 2px #e7c3c2}
.feature-title{left:717px;font-size:17px;font-weight:400;color:var(--red)}
.feature-text{left:717px;width:392px;font-size:12px;line-height:19.5px;color:var(--muted)}
.read-more{left:1037px;font-size:11.5px;color:var(--link);text-decoration:underline;font-weight:700}
.read-more span{text-decoration:none;display:inline-block;margin-left:6px}

/* prices */
.prices{left:0;top:1187px;width:1200px;height:529px;background:var(--grey-bg);border-top:1px solid #ddd;border-bottom:1px solid #ddd}
.card{top:1318px;width:241px;height:357px;background:#fff;border:1px solid #c9c9c9;padding:6px}
.card-inner{position:relative;width:100%;height:100%;border:1px solid #ddd;overflow:hidden}
.card-head{position:absolute;left:0;top:0;width:100%;height:124px;background:linear-gradient(#c75a58,#b8413f)}
.card-time{position:absolute;top:22px;width:100%;text-align:center;color:#fff;font-family:"Abel",Arial,sans-serif;font-size:31px}
.card-price{position:absolute;left:50%;top:72px;width:118px;height:118px;margin-left:-59px;border-radius:50%;background:#fff;box-shadow:0 0 0 5px rgba(255,255,255,.5);display:flex;align-items:center;justify-content:center;color:var(--navy);font-weight:700;font-size:35px}
.card-name{position:absolute;top:202px;width:100%;text-align:center;color:var(--navy);font-size:19px;font-weight:700}
.card-text{position:absolute;top:230px;left:12px;right:12px;text-align:center;font-size:11.5px;line-height:17px;color:#555}
.card-btn{position:absolute;left:50%;top:288px;margin-left:-53px;width:106px;height:32px;background:var(--red);color:#fff;font-size:13px;display:flex;align-items:center;justify-content:center}

/* testimonials */
.avatar{left:547px;top:1853px;width:106px;height:106px;border-radius:50%;border:2px dashed #999;padding:6px}
.avatar div{width:100%;height:100%;border-radius:50%;background:linear-gradient(#dfe4ea,#9aa3ad)}
.quote-mark{left:258px;top:1965px;font-family:Georgia,serif;font-size:56px;color:#e2c8c8;line-height:1}
.quote{left:280px;top:1977px;width:640px;text-align:center;font-size:13px;line-height:22px;color:#333}
.quote-name{left:0;top:2025px;width:1200px;text-align:center;font-size:13px;font-weight:700;color:#222}
.dot{top:2066px;width:12px;height:12px;border-radius:50%;background:var(--red)}
.dot.on{background:var(--navy)}
.test-left{left:0;top:2005px;width:257px;height:109px;background:linear-gradient(90deg,#8a7fa8,#b9b3b0 50%,rgba(255,255,255,0))}
.test-right{left:898px;top:1957px;width:302px;height:157px;background:linear-gradient(270deg,#f3f3f3,#e9c8c7 45%,#c9d78f 70%,rgba(255,255,255,0))}

/* footer */
.footer{left:0;top:2114px;width:1200px;height:257px;background:var(--footer)}
.f-head{top:2150px;font-size:18px;font-weight:400;color:#fff}
.f-rule{top:2183px;height:0;border-top:1px dotted rgba(255,255,255,.5)}
.f-sep{top:2150px;width:0;height:190px;border-left:1px solid rgba(255,255,255,.18)}
.f-links{left:82px;top:2197px;list-style:none}
.f-links li{font-size:13px;color:#fff;height:24px;line-height:24px}
.f-links li::before{content:"›";margin-right:10px}
.field{left:313px;width:224px;background:#fff;border-radius:3px;font-size:12px;color:#444;padding:5px 8px}
.submit{left:313px;top:2306px;width:63px;height:23px;background:var(--red-light);color:#fff;font-size:12px;border-radius:3px;display:flex;align-items:center;justify-content:center}
.c-row{left:642px;display:flex;gap:12px;color:#fff;font-size:13px;line-height:18px}
.f-brand{left:985px;top:2153px;width:128px;height:128px;border-radius:50%;background:#4a4fa0;border:3px solid #6e73b8;display:flex;align-items:center;justify-content:center;text-align:center;color:#fff;font-family:"Kreon",Georgia,serif;font-weight:700;font-size:24px;line-height:1}
.social{top:2300px;width:32px;height:32px;border-radius:50%;background:var(--red)}
.bottom{left:0;top:2371px;width:1200px;height:35px;background:var(--red);color:#fff;font-size:11.5px}
.bottom span{position:absolute;top:11px}
</style>
</head>
<body>
<div class="page">

  <!-- top bar -->
  <div class="abs quick-btn">
    <svg width="12" height="12" viewBox="0 0 12 12"><rect x="1" y="2" width="10" height="9" fill="none" stroke="#fff" stroke-width="1.4"/><line x1="1" y1="5" x2="11" y2="5" stroke="#fff" stroke-width="1.4"/></svg>
    QUICK INQUERY
  </div>
  <div class="abs top-contact" style="left:752px">
    <svg width="14" height="10" viewBox="0 0 14 10"><rect x=".7" y=".7" width="12.6" height="8.6" fill="none" stroke="#1c1a8f" stroke-width="1.4"/><path d="M1 1l6 5 6-5" fill="none" stroke="#1c1a8f" stroke-width="1.4"/></svg>
    kestrelwaymassage@fernmail.net
  </div>
  <div class="abs top-contact" style="left:1004px">
    <svg width="14" height="14" viewBox="0 0 14 14"><path d="M3 1l3 3-2 2c1 2 2 3 4 4l2-2 3 3-2 2C6 13 1 8 1 3z" fill="#1c1a8f"/></svg>
    (206) 555-0148
  </div>

  <!-- navigation -->
  <nav class="abs nav">
    <span class="nav-item active" style="left:80px">HOME</span>
    <span class="nav-star" style="left:170px">★</span>
    <span class="nav-item" style="left:218px">ABOUT US</span>
    <span class="nav-star" style="left:331px">★</span>
    <span class="nav-item" style="left:383px">SERVICES</span>
    <span class="nav-star" style="left:496px">★</span>
    <span class="nav-star" style="left:693px">★</span>
    <span class="nav-item" style="left:728px">PRICES</span>
    <span class="nav-star" style="left:803px">★</span>
    <span class="nav-item" style="left:837px">PHOTO GALLERY</span>
    <span class="nav-star" style="left:987px">★</span>
    <span class="nav-item" style="left:1023px">CONTACT US</span>
  </nav>
  <div class="abs brand">KESTREL<br>WAY</div>

  <!-- hero -->
  <div class="abs hero" role="img" aria-label="Spa still life with towels, candle, flowers and stones on the left; a smiling woman resting on a white towel on the right"></div>
  <div class="abs hero-title">MASSAGE</div>
  <div class="abs hero-sub">THERAPY</div>
  <div class="abs hero-tag">We come to you</div>

  <!-- about -->
  <h2 class="abs sec-title" style="top:688px"><span class="r">ABOUT</span> <span class="n">US</span></h2>
  <svg class="abs divider" style="top:732px" viewBox="0 0 280 24">
    <g stroke="#e3a9a7" stroke-width="1"><line x1="0" y1="10" x2="122" y2="10"/><line x1="0" y1="14" x2="122" y2="14"/><line x1="158" y1="10" x2="280" y2="10"/><line x1="158" y1="14" x2="280" y2="14"/></g>
    <circle cx="140" cy="12" r="11" fill="#333"/><circle cx="140" cy="12" r="8" fill="none" stroke="#fff" stroke-width="1"/>
  </svg>
  <p class="abs about-intro">We are a male and female mobile massage team. Our names are Paul and Lina. Kestrel Way is a Seattle based mobile massage service. Our massage is offered to the community with a goal of facilitating balance within each individual. We specialize in integrated Pain management, and sports/medical massage therapy. Every client's first assessment is attended by our male and female massage therapist team. Depending on the goals identified for an individual determines which therapist will be assigned to provide treatment, if not both.</p>

  <div class="abs about-photo" role="img" aria-label="Pink gerbera daisies with stacked grey spa stones and scattered petals"></div>

  <div class="abs feature-icon" style="top:861px">
    <svg width="72" height="72" viewBox="0 0 72 72"><g fill="#fff"><circle cx="31" cy="22" r="5"/><rect x="18" y="42" width="36" height="4"/><rect x="20" y="46" width="3" height="9"/><rect x="49" y="46" width="3" height="9"/><path d="M27 29h8l4 8h-12z"/><rect x="38" y="36" width="14" height="5" rx="2"/></g></svg>
  </div>
  <h3 class="abs feature-title" style="top:856px">Why We Stand Out?</h3>
  <p class="abs feature-text" style="top:882px">Kestrel Way is a Seattle based mobile massage service. Our massage is offered to the community with a goal of facilitating balance within each individual.</p>
  <a class="abs read-more" style="top:933px">Read More<span>»</span></a>

  <div class="abs feature-icon" style="top:964px">
    <svg width="72" height="72" viewBox="0 0 72 72"><g fill="#fff"><circle cx="26" cy="25" r="5"/><circle cx="46" cy="25" r="5"/><path d="M19 33h14v14h-4v-6h-6v6h-4z"/><path d="M39 33h14v14h-4v-6h-6v6h-4z"/><rect x="30" y="36" width="12" height="3"/></g></svg>
  </div>
  <h3 class="abs feature-title" style="top:959px">Our Passion.</h3>
  <p class="abs feature-text" style="top:983px">Here at Kestrel Way, we have a great passion for Postural Resoration and how it is integrated into an individual's Massage treatment. We pride ourselves in being natural</p>
  <a class="abs read-more" style="top:1032px">Read More<span>»</span></a>

  <div class="abs feature-icon" style="top:1067px">
    <svg width="72" height="72" viewBox="0 0 72 72"><g fill="none" stroke="#fff" stroke-width="2.5"><rect x="32" y="20" width="22" height="16"/><line x1="24" y1="30" x2="36" y2="26"/></g><g fill="#fff"><circle cx="23" cy="24" r="4"/><path d="M18 30h9v20h-3v-10h-3v10h-3z"/><rect x="40" y="36" width="3" height="14"/></g></svg>
  </div>
  <h3 class="abs feature-title" style="top:1060px">Our Education.</h3>
  <p class="abs feature-text" style="top:1083px">We are both Graduates of Venmora, school of massage therapy. We have continuing education in medical massage, myofacial release, trigger point therapy, postural restoration, anatomy</p>
  <a class="abs read-more" style="top:1133px">Read More<span>»</span></a>

  <!-- prices -->
  <section class="abs prices"></section>
  <h2 class="abs sec-title" style="top:1214px"><span class="r">OUR</span> <span class="n">PRICES</span></h2>
  <svg class="abs divider" style="top:1258px" viewBox="0 0 280 24">
    <g stroke="#e3a9a7" stroke-width="1"><line x1="0" y1="10" x2="122" y2="10"/><line x1="0" y1="14" x2="122" y2="14"/><line x1="158" y1="10" x2="280" y2="10"/><line x1="158" y1="14" x2="280" y2="14"/></g>
    <circle cx="140" cy="12" r="11" fill="#333"/><circle cx="140" cy="12" r="8" fill="none" stroke="#fff" stroke-width="1"/>
  </svg>

  <div class="abs card" style="left:80px"><div class="card-inner"><div class="card-head"></div><div class="card-time">60 minutes</div><div class="card-price">$75</div><div class="card-name">MASSAGE THERAPY</div><p class="card-text">Both Lina and I worked as behavioral health professionals that specialized in life skills mentoring for</p><div class="card-btn">Read More</div></div></div>
  <div class="abs card" style="left:346px"><div class="card-inner"><div class="card-head"></div><div class="card-time">90 minutes</div><div class="card-price">$95</div><div class="card-name">MASSAGE THERAPY</div><p class="card-text">Both Lina and I worked as behavioral health professionals that specialized in life skills mentoring for</p><div class="card-btn">Read More</div></div></div>
  <div class="abs card" style="left:613px"><div class="card-inner"><div class="card-head"></div><div class="card-time">120 minutes</div><div class="card-price">$120</div><div class="card-name">MASSAGE THERAPY</div><p class="card-text">Both Lina and I worked as behavioral health professionals that specialized in life skills mentoring for</p><div class="card-btn">Read More</div></div></div>
  <div class="abs card" style="left:879px"><div class="card-inner"><div class="card-head"></div><div class="card-time">150 minutes</div><div class="card-price">$150</div><div class="card-name">MASSAGE THERAPY</div><p class="card-text">Both Lina and I worked as behavioral health professionals that specialized in life skills mentoring for</p><div class="card-btn">Read More</div></div></div>

  <!-- testimonials -->
  <h2 class="abs sec-title" style="top:1750px"><span class="r">CLIENT</span> <span class="n">TESTIMONIALS</span></h2>
  <svg class="abs divider" style="top:1793px" viewBox="0 0 280 24">
    <g stroke="#e3a9a7" stroke-width="1"><line x1="0" y1="10" x2="122" y2="10"/><line x1="0" y1="14" x2="122" y2="14"/><line x1="158" y1="10" x2="280" y2="10"/><line x1="158" y1="14" x2="280" y2="14"/></g>
    <circle cx="140" cy="12" r="11" fill="#333"/><circle cx="140" cy="12" r="8" fill="none" stroke="#fff" stroke-width="1"/>
  </svg>
  <div class="abs avatar"><div role="img" aria-label="Portrait of the client"></div></div>
  <div class="abs test-left" role="img" aria-label="Rolled lavender towel with stacked stones and lavender sprigs"></div>
  <div class="abs test-right" role="img" aria-label="White towels with green candles and a pink orchid"></div>
  <div class="abs quote-mark">“</div>
  <p class="abs quote">The most important thing to 'us', as Licenced providers is to get you on to our table to show you our skills. But a good therapist never forgets that it's not about what we do for you, but what we can facilitate for you.</p>
  <div class="abs quote-name">Ms. Nola Brisk</div>
  <span class="abs dot" style="left:569px"></span>
  <span class="abs dot on" style="left:594px"></span>
  <span class="abs dot" style="left:619px"></span>

  <!-- footer -->
  <footer class="abs footer"></footer>
  <h4 class="abs f-head" style="left:82px">Quick Links</h4>
  <div class="abs f-rule" style="left:82px;width:125px"></div>
  <ul class="abs f-links">
    <li>Home</li><li>About US</li><li>Services</li><li>Prices</li><li>Photo Gallery</li><li>Contact Us</li>
  </ul>
  <div class="abs f-sep" style="left:257px"></div>

  <h4 class="abs f-head" style="left:311px">Quick Inquiry</h4>
  <div class="abs f-rule" style="left:311px;width:226px"></div>
  <div class="abs field" style="top:2199px;height:24px">Name</div>
  <div class="abs field" style="top:2229px;height:24px">Email</div>
  <div class="abs field" style="top:2259px;height:40px">Message</div>
  <div class="abs submit">Submit</div>
  <div class="abs f-sep" style="left:589px"></div>

  <h4 class="abs f-head" style="left:642px">Contact Details</h4>
  <div class="abs f-rule" style="left:642px;width:236px"></div>
  <div class="abs c-row" style="top:2204px">
    <svg width="10" height="14" viewBox="0 0 10 14"><path d="M5 0a5 5 0 0 1 5 5c0 4-5 9-5 9S0 9 0 5a5 5 0 0 1 5-5z" fill="#fff"/><circle cx="5" cy="5" r="2" fill="#26216b"/></svg>
    <span>Lorem ipsum dolor sit amet,<br>consectetuer adipiscing elit, sed<br>diam nonummy nibh .</span>
  </div>
  <div class="abs c-row" style="top:2264px">
    <svg width="13" height="13" viewBox="0 0 14 14"><path d="M3 1l3 3-2 2c1 2 2 3 4 4l2-2 3 3-2 2C6 13 1 8 1 3z" fill="#fff"/></svg>
    <span>(206) 555-0148</span>
  </div>
  <div class="abs c-row" style="top:2296px">
    <svg width="13" height="10" viewBox="0 0 14 10"><rect x=".7" y=".7" width="12.6" height="8.6" fill="none" stroke="#fff" stroke-width="1.4"/><path d="M1 1l6 5 6-5" fill="none" stroke="#fff" stroke-width="1.4"/></svg>
    <span>kestrelwaymassage@fernmail.net</span>
  </div>
  <div class="abs f-sep" style="left:924px"></div>

  <div class="abs f-brand">KESTREL<br>WAY</div>
  <span class="abs social" style="left:1003px"></span>
  <span class="abs social" style="left:1043px"></span>
  <span class="abs social" style="left:1083px"></span>

  <div class="abs bottom">
    <span style="left:82px">Copyright © 2015 kestrelwaymassage | All Right Reserved.</span>
    <span style="left:895px">Terms &amp; Conditions</span>
    <span style="left:1021px">|</span>
    <span style="left:1039px">Privacy Policy</span>
  </div>
</div>
</body>
</html>
```